Luxury Home Builder looking for an Exciting Homes Portfolio

We have a number of custom homes that we have completed over the years, and we want to give prospective clients are colorful and exciting catalog of our previous homes. I will provide access to the dropbox with all the photos. Need to get as many photos of homes in the catalog as possible. Please use vandrelluxuryhomes.com for pictures, lots of them in the portfolio, projects in progress, spec homes are available. I will provide full files to the winner. Need a very hip catalog to give out at events, and marketing venues.

Target Market(s)

High Net Worth Individuals looking for luxury homes

Industry/Entity Type

Real Estate Development

Requirements
Must have
• Photos of our project, please use vandrelluxuryhomes.com to get the photos, and will provide access to full pictures on dropbox to the winner.
• Logo must be incorporated.
Nice to have
• Clarification, website is not for design, but for the purposes of getting the photos. this has to be a very cool portfolio.

```html
<!DOCTYPE html>
<html lang="en">
<head>
<meta charset="utf-8">
<title>Vandrel – About</title>
<link rel="stylesheet" href="https://fonts.googleapis.com/css2?family=Roboto:wght@400;500;700&display=swap">
<style>
  :root {
    --backdrop: #d6d7d9;
    --paper: #ffffff;
    --navy: #1d4f8f;
    --ink: #6b6f75;
    --sky: #5c9be0;
    --pool: #1aa6e0;
    --deck: #d9d0bd;
    --foliage: #3f7a2c;
  }
  * { margin: 0; padding: 0; box-sizing: border-box; }
  html, body {
    width: 1200px; height: 801px; overflow: hidden;
    background: var(--backdrop);
    font-family: "Roboto", Arial, sans-serif;
  }
  .spread {
    position: absolute; left: 50px; top: 204px;
    width: 1100px; height: 393px;
    background: var(--paper);
    display: flex;
  }
  .spread-photo {
    position: relative;
    width: 844px; height: 100%;
    background:
      linear-gradient(180deg, rgba(92,155,224,0.95) 0%, rgba(150,190,230,0.9) 28%, rgba(236,238,240,0.9) 40%, rgba(200,206,210,0.85) 50%, rgba(26,166,224,0.95) 58%, rgba(40,150,205,0.95) 72%, rgba(217,208,189,1) 80%, rgba(200,190,170,1) 100%),
      linear-gradient(90deg, transparent 70%, var(--foliage) 100%);
    background-blend-mode: normal;
  }
  .spread-photo::after {
    content: ""; position: absolute; top: 0; bottom: 0; left: 540px; width: 30px;
    background: linear-gradient(90deg, rgba(0,0,0,0) 0%, rgba(0,0,0,0.12) 50%, rgba(0,0,0,0) 100%);
  }
  .about-panel {
    position: relative; flex: 1; height: 100%;
  }
  .section-label {
    position: absolute; top: 17px; right: 0;
    display: flex; align-items: center; gap: 8px;
    font-size: 5.6px; font-weight: 700; letter-spacing: 0.4px;
    color: var(--navy);
  }
  .section-label .bar { width: 62px; height: 5px; background: var(--navy); }
  .headline {
    position: absolute; left: 26px; top: 122px;
    padding-left: 8px; border-left: 1px solid var(--navy);
    font-size: 12.5px; font-weight: 500; line-height: 12.5px;
    letter-spacing: 0.4px; color: var(--navy);
  }
  .headline strong { font-weight: 700; }
  .copy {
    position: absolute; left: 26px; top: 161px; width: 210px;
    font-size: 5.6px; line-height: 7.3px; color: var(--ink);
    text-align: justify;
  }
  .copy h3 {
    font-size: 7px; font-weight: 700; color: var(--navy);
    letter-spacing: 0.2px; margin: 9px 0 8px;
  }
  .page-number {
    position: absolute; right: 30px; bottom: 10px;
    font-size: 6px; color: var(--ink);
  }
</style>
</head>
<body>
  <main class="spread">
    <div class="spread-photo" role="img" aria-label="Photo of a white luxury home with dark roof, rectangular pool, travertine deck, wicker lounge seating and palm trees under a blue sky"></div>
    <section class="about-panel">
      <div class="section-label">ABOUT VANDREL <span class="bar"></span></div>
      <h2 class="headline">THE MAIN SOURCE OF<br>KNOWLEDGE IS <strong>EXPERIENCE</strong></h2>
      <div class="copy">
        <p>When high net worth individuals are considering building a home, it generally isn't the price that they're afraid of. It's the ordeal they expect to have to go through to have it completed to their satisfaction. Indeed, it is fair to say that the more expensive the home—the more that quality and detailing matter—the greater the likelihood that there will be unexpected costs and delays. For our clients, Vandrel Inter-Development, Inc., has put those fears to rest. We have created many of the most prestigious, most luxurious homes in Dade County, we have spared our clients the anguish that so many new home buyers experience.</p>
        <h3>WE'RE WITH YOU EVERY STEP OF THE WAY</h3>
        <p>Vandrel isn't your typical builder. You see, our Founder and President, Martin Ortega, is trained as an architect and a builder. At Vandrel, a project is conceived and designed with a unique perspective, seeing it in terms of both idea and execution. They know precisely how much their plans will cost to bring to fruition, how long the project will take, and how to make certain the construction and detailing are true to the architect's and client's vision. More than that, we work so closely with our clients to ensure that every detail—every tile, faucet, doorknob and appliance—is chosen and installed with great care and skill and is faithful to the overall design scheme. In short, we are with you every step of the way, making sure your new home lives up to your every expectation.</p>
      </div>
      <span class="page-number">2</span>
    </section>
  </main>
</body>
</html>
```